Moravel Aesthetic Doctor

I require an elegant, luxurious looking business card for my aesthetic business. I am a doctor and that will set me aside from competitors. I am planning to provide home and spa based treatments to clients with high expectations. I have attached my logo.

```html
<!DOCTYPE html>
<html lang="en">
<head>
<meta charset="utf-8">
<title>Moravel Aesthetic Doctor – Business Card</title>
<link rel="stylesheet" href="https://fonts.googleapis.com/css2?family=Quicksand:wght@400;500;600&display=swap">
<style>
  :root {
    --backdrop: #2bbcd0;
    --card: #ffffff;
    --ink-grey: #8e8e92;
    --ink-dark: #3a3a3e;
    --accent: #2aa6e0;
    --accent-soft: #8fd0f0;
  }
  * { box-sizing: border-box; margin: 0; padding: 0; }
  html, body { width: 1200px; height: 800px; overflow: hidden; }
  body {
    background: var(--backdrop);
    font-family: "Quicksand", sans-serif;
    color: var(--ink-dark);
    display: flex;
    align-items: center;
    justify-content: center;
    gap: 80px;
  }
  .card {
    width: 360px;
    height: 600px;
    background: var(--card);
    border-radius: 34px;
    box-shadow: 0 10px 30px rgba(0,60,80,0.25);
    display: flex;
    flex-direction: column;
    align-items: center;
    text-align: center;
  }
  .card--front { justify-content: center; }
  .card--back { padding: 56px 30px 40px; }

  .brand { display: flex; flex-direction: column; align-items: center; }
  .brand__mark {
    width: 78px; height: 78px;
    border: 2px solid var(--ink-grey);
    border-radius: 50%;
    margin-bottom: 18px;
  }
  .brand__name {
    font-weight: 500;
    color: var(--ink-grey);
    letter-spacing: 0.08em;
    line-height: 1.15;
    text-transform: uppercase;
  }
  .brand__name--large { font-size: 38px; }
  .brand__name--small { font-size: 28px; }
  .brand__sub { display: block; font-size: 0.5em; letter-spacing: 0.12em; }

  .front__tagline {
    margin-top: 14px;
    font-size: 15px;
    color: var(--ink-grey);
  }

  .doctor__name { font-size: 17px; font-weight: 600; color: var(--ink-dark); }
  .doctor__name small { font-size: 13px; font-weight: 400; color: var(--ink-grey); }
  .doctor__title { margin-top: 4px; font-size: 12.5px; color: var(--ink-dark); }
  .divider { width: 14px; height: 3px; background: var(--accent); margin: 14px 0 22px; }

  .services {
    margin-top: 22px;
    font-size: 13px;
    line-height: 1.55;
    color: var(--ink-dark);
    list-style: none;
  }
  .icons { display: flex; gap: 22px; margin: 22px 0 16px; }
  .icon {
    width: 26px; height: 26px;
    border-radius: 50%;
    background: var(--accent);
    display: flex; align-items: center; justify-content: center;
  }
  .icon svg { width: 14px; height: 14px; }
  .contacts { list-style: none; font-size: 15px; line-height: 1.7; color: var(--ink-dark); }
  .contacts .highlight { color: var(--accent); }
</style>
</head>
<body>
  <section class="card card--front" aria-label="Card front">
    <div class="brand">
      <span class="brand__mark"></span>
      <p class="brand__name brand__name--large">Moravel<span class="brand__sub">Aesthetic Doctor</span></p>
    </div>
    <p class="front__tagline">Home and Spa Based Treatments</p>
  </section>

  <section class="card card--back" aria-label="Card back">
    <p class="doctor__name">Dr. Elena Varsk <small>MRCPCH MD</small></p>
    <p class="doctor__title">Australasian Diploma of Aesthetic Medicine</p>
    <span class="divider"></span>

    <div class="brand">
      <span class="brand__mark"></span>
      <p class="brand__name brand__name--small">Moravel<span class="brand__sub">Aesthetic Doctor</span></p>
    </div>

    <ul class="services">
      <li>Dermal injectables | Plasma facials</li>
      <li>Microneedling | Skin boosters</li>
      <li>Excessive sweating</li>
      <li>Home and Spa Based Treatments</li>
    </ul>

    <div class="icons">
      <span class="icon" aria-label="Phone">
        <svg viewBox="0 0 24 24"><path fill="#fff" d="M6.6 10.8a15 15 0 0 0 6.6 6.6l2.2-2.2c.3-.3.7-.4 1-.2 1.1.4 2.3.6 3.6.6.6 0 1 .4 1 1V20c0 .6-.4 1-1 1A17 17 0 0 1 3 4c0-.6.4-1 1-1h3.5c.6 0 1 .4 1 1 0 1.3.2 2.5.6 3.6.1.3 0 .7-.2 1z"/></svg>
      </span>
      <span class="icon" aria-label="Email">
        <svg viewBox="0 0 24 24"><rect x="3" y="6" width="18" height="12" rx="1.5" fill="#fff"/><path d="M3.5 6.5 12 13l8.5-6.5" stroke="#2aa6e0" stroke-width="1.6" fill="none"/></svg>
      </span>
      <span class="icon" aria-label="Website">
        <svg viewBox="0 0 24 24"><circle cx="12" cy="12" r="8" stroke="#fff" stroke-width="2" fill="none"/><path d="M4 12h16M12 4c3 3 3 13 0 16M12 4c-3 3-3 13 0 16" stroke="#fff" stroke-width="1.6" fill="none"/></svg>
      </span>
    </div>

    <ul class="contacts">
      <li>0800 555 019</li>
      <li>elena@moravel.co.nz</li>
      <li>www.<span class="highlight">moravel</span>.co.nz</li>
    </ul>
  </section>
</body>
</html>
```